Automotive Business Card Design

I would just like a automotive themed card. nothing too extravagant, but catchy.

needs to say something about doing roadside assistance,mobile repairs, Diesel repairs, and Fleet maintenance

it can be single sided or double sided. no preference there.

Industry/Entity Type

Automotive

Contact Information for Business Card

Dean Marlowe
phone 534 861 2093
Name: Brightpath Automotive & Diesel Repair

```html
<!DOCTYPE html>
<html lang="en">
<head>
<meta charset="utf-8">
<title>Brightpath Automotive &amp; Diesel Repair – Business Card</title>
<link href="https://fonts.googleapis.com/css2?family=Exo+2:ital,wght@0,400;0,700;1,300;1,400;1,800&display=swap" rel="stylesheet">
<style>
  :root {
    --page-bg: #e9e6e2;
    --card-grey: #5b5b5b;
    --panel-black: #050505;
    --engine-steel: #6e7480;
    --photo-dark: #1d2024;
    --photo-mid: #4a4f56;
    --band-silver: #c9cbcd;
    --band-light: #e6e7e8;
    --ink-white: #ffffff;
    --ink-soft: #eceff1;
    --ink-black: #111111;
  }
  * { margin: 0; padding: 0; box-sizing: border-box; }
  html, body {
    width: 1200px; height: 1037px; overflow: hidden;
    background: var(--page-bg);
    font-family: "Exo 2", "Segoe UI", sans-serif;
  }
  .sheet {
    position: relative; width: 1200px; height: 1037px;
  }
  .card {
    position: absolute; left: 270px; width: 660px; height: 378px;
    overflow: hidden;
    box-shadow: 0 6px 18px rgba(0,0,0,.22);
  }
  /* Back: services */
  .card--services { top: 100px; background: var(--card-grey); }
  .services__title {
    position: absolute; left: 44px; top: 34px;
    color: var(--ink-white); font-weight: 800; font-style: italic;
    font-size: 36px; letter-spacing: .5px;
  }
  .services__list {
    position: absolute; left: 44px; top: 92px; list-style: none;
    color: var(--ink-soft); font-style: italic; font-weight: 300;
    font-size: 25px; line-height: 30px;
  }
  .services__phone {
    position: absolute; left: 44px; top: 262px;
    color: var(--ink-soft); font-weight: 400; font-size: 28px; letter-spacing: 3px;
  }
  .services__engine {
    position: absolute; right: 20px; top: 24px; width: 270px; height: 332px;
    background: radial-gradient(ellipse at 55% 50%, var(--engine-steel) 0%, #2b2e33 45%, var(--panel-black) 75%);
  }
  /* Front: identity */
  .card--identity {
    top: 560px;
    background: linear-gradient(160deg, var(--photo-mid) 0%, var(--photo-dark) 55%, #0c0d0f 100%);
  }
  .identity__photo { position: absolute; inset: 0; }
  .identity__name {
    position: absolute; right: 34px; top: 28px;
    color: var(--ink-white); font-weight: 700; font-size: 30px; letter-spacing: 4px;
  }
  .identity__phone {
    position: absolute; right: 62px; top: 70px;
    color: var(--ink-white); font-size: 20px; letter-spacing: 3px;
  }
  .identity__band {
    position: absolute; left: 0; right: 0; top: 244px; height: 62px;
    background: linear-gradient(180deg, var(--band-light), var(--band-silver));
    display: flex; align-items: center; justify-content: center;
  }
  .identity__company {
    color: var(--ink-black); font-weight: 800; font-style: italic;
    font-size: 23px; letter-spacing: .5px; text-transform: uppercase; white-space: nowrap;
  }
</style>
</head>
<body>
<main class="sheet">
  <section class="card card--services">
    <h2 class="services__title">SERVICES</h2>
    <ul class="services__list">
      <li>Roadside assistance</li>
      <li>Mobile repairs</li>
      <li>Diesel repairs</li>
      <li>And Fleet maintenance</li>
    </ul>
    <p class="services__phone">534 861 2093</p>
    <div class="services__engine" role="img" aria-label="Photo of a chrome car engine on a black background"></div>
  </section>

  <section class="card card--identity">
    <div class="identity__photo" role="img" aria-label="Photo of a mechanic's hand turning a wrench under an open car hood"></div>
    <h1 class="identity__name">Dean Marlowe</h1>
    <p class="identity__phone">534 861 2093</p>
    <div class="identity__band">
      <p class="identity__company">Brightpath Automotive &amp; Diesel Repair</p>
    </div>
  </section>
</main>
</body>
</html>
```